Hvac and insulation company needs good looking business card design

We are hvac and insulation company and looking for a new business cards that look to today standards designs

Target Market(s)

homeowners

Industry/Entity Type

Hvac

Contact Information for Business Card

Name: Walter Brinoku
Home comfort consultant
address: 4827 Dunmore St #215 Oakland, CA 94619
office: 888-316-2790
cell: 510-742-3185
Lic.# 584261
Email: walter@corvane-hvac.com
Web: corvane-hvac.com

Requirements
Must have
• clean and sleek look
Nice to have
• simple with a clean look
Should not have
• to busy business card

```html
<!DOCTYPE html>
<html lang="en">
<head>
<meta charset="utf-8">
<title>Corvane Home Solutions – Business Card</title>
<link href="https://fonts.googleapis.com/css2?family=Arimo:wght@400;700&display=swap" rel="stylesheet">
<style>
  :root {
    --stage: #242424;
    --orange: #f5841f;
    --white: #ffffff;
    --ink: #222222;
    --grey: #7a7a7a;
    --rule: #9a9a9a;
  }
  * { margin: 0; padding: 0; box-sizing: border-box; }
  html, body { width: 1200px; height: 900px; overflow: hidden; }
  body {
    background: var(--stage);
    font-family: "Arimo", Arial, sans-serif;
    position: relative;
  }
  .card {
    position: absolute;
    top: 306px;
    width: 439px;
    height: 271px;
    border-radius: 12px;
    box-shadow: 2px 4px 6px rgba(0,0,0,.55);
  }
  .card--front { left: 149px; background: var(--white); color: var(--ink); }
  .card--back { left: 609px; background: var(--orange); color: var(--white); }

  .brand { position: absolute; right: 25px; top: 50px; text-align: right; }
  .brand__name {
    display: flex; align-items: center; justify-content: flex-end; gap: 10px;
    font-size: 46px; font-weight: 400; color: var(--orange); line-height: 1;
  }
  .brand__mark { width: 22px; height: 22px; background: var(--orange); }
  .brand__tagline {
    font-size: 14px; letter-spacing: 2px; color: var(--grey); margin-top: 2px;
  }

  .person { position: absolute; left: 21px; top: 152px; width: 394px; }
  .person__name { font-size: 18.5px; font-weight: 700; color: var(--orange); }
  .person__role {
    display: flex; align-items: center; gap: 5px;
    font-size: 12.5px; margin-top: 2px;
  }
  .person__role::after { content: ""; flex: 1; height: 1px; background: var(--rule); }
  .license { position: absolute; right: 25px; top: 154px; font-size: 13px; }
  .license__label { color: var(--orange); }

  .address { position: absolute; left: 21px; top: 216px; font-size: 13px; line-height: 16px; }
  .contacts {
    position: absolute; right: 24px; top: 201px; list-style: none;
    font-size: 13px; line-height: 16px; text-align: right;
  }
  .contacts li { display: flex; align-items: center; justify-content: flex-end; gap: 2px; }
  .contacts svg { width: 10px; height: 10px; fill: var(--orange); }

  .back-brand {
    position: absolute; left: 0; right: 0; top: 100px;
    display: flex; align-items: center; justify-content: center; gap: 14px;
    font-size: 58px; font-weight: 400; line-height: 1;
  }
  .back-brand__mark { width: 28px; height: 28px; background: var(--white); }
  .website {
    position: absolute; left: 0; right: 0; top: 224px;
    text-align: center; font-size: 13px;
  }
</style>
</head>
<body>
  <section class="card card--front">
    <div class="brand">
      <div class="brand__name"><span class="brand__mark"></span>corvane</div>
      <div class="brand__tagline">home solutions</div>
    </div>
    <div class="license"><span class="license__label">LIC.</span># 584261</div>
    <div class="person">
      <div class="person__name">Walter Brinoku</div>
      <div class="person__role">Home Comfort Consultant</div>
    </div>
    <address class="address" style="font-style:normal">4827 Dunmore St<br>#215 Oakland, CA 94619</address>
    <ul class="contacts">
      <li>888-316-2790
        <svg viewBox="0 0 10 10"><path d="M1 4c0-2 2-3 4-3s4 1 4 3H7V3H3v1zM2 5h6l1 4H1z"/></svg></li>
      <li>510-742-3185
        <svg viewBox="0 0 10 10"><path d="M2.5 0h5v10h-5zM3.5 1v7h3V1z"/></svg></li>
      <li>walter@corvane-hvac.com
        <svg viewBox="0 0 10 10"><path d="M0 2h10v1L5 6 0 3zM0 4l5 3 5-3v4H0z"/></svg></li>
    </ul>
  </section>

  <section class="card card--back">
    <div class="back-brand"><span class="back-brand__mark"></span>corvane</div>
    <div class="website">www.corvane-hvac.com</div>
  </section>
</body>
</html>
```